Etiketten für Honig
Wir können nur volle Punktzahl geben. Roswitha ist selbst Ideenreich, wirklich nett und setzte unsere Ideen schnell und engagiert um. Hat echt Spass gemacht mit ihr zu arbeiten.
Zielgruppe
Es scheint Missverständnisse zu geben weshalb ich das Briefing wohl ändern muss.
see below for English translation
Wir sind eine kleine Imkerei, die von der Liebhaberei in den Nebenerwerb wechselt. Wir verkaufen verschiedene Sortenhonige und Honigzubereitungen (siehe Webseite) im vorwiegend ländlichen Raum des Münsterlandes.
Entsprechend unseres Standortes und unserer Kundschaft benötigen wir ein klassisch ländliches Design. Hierfür haben wir auch bereits ein Logo welches verwendet werden muss.
English
There seems to be some misunderstanding, so I guess I'll have to change the briefing.
We are a small apiary that changes from hobby to sideline. We sell different types of honey and honey preparations (e.g. honey with raspberry) in a predominantly rural area of the Münsterland (Muensterland).
According to our location and our clientele, we need a classic rural design. We already have a logo which must be used.
Aufgabenstellung
Wir möchten ein rechteckiges Etikett mit Gewährverschluss das für verschiedene Sorten adoptierbar ist. Zum Beispiel durch den Austausch der Sortenbezeichnung und eine farbliche Veränderung.
Das Design soll später auf Naturpapier oder Graspapier gedruckt werden. Das Logo muss auf Etikett und Gewährverschluss abgebildet werden.
We would like a rectangular label with a guarantee seal that is adoptable for different varieties. For example, by exchanging the variety designation and changing the color.
The design will later be printed on uncoated paper or grass paper. The logo must be shown on the label and guarantee seal.

```html
<!DOCTYPE html>
<html lang="de">
<head>
<meta charset="utf-8">
<title>Etikett Linde – Imkerei Wiesbrook</title>
<link rel="stylesheet" href="https://fonts.googleapis.com/css2?family=Quicksand:wght@500;700&family=Kaushan+Script&family=Caveat+Brush&display=swap">
<style>
  :root {
    --honey: #c47c12;
    --gold: #f5c518;
    --paper: #ffffff;
    --deco: #d9a35c;
    --ink: #1a1a1a;
  }
  html, body { margin: 0; padding: 0; overflow: hidden; background: var(--paper); }
  .label { position: relative; width: 1062px; height: 1200px; overflow: hidden; background: var(--paper); font-family: "Quicksand", sans-serif; }

  /* guarantee seal */
  .seal-ring { position: absolute; left: 352px; top: -4px; width: 394px; height: 394px; border-radius: 50%; background: var(--honey); }
  .seal-face { position: absolute; left: 397px; top: 41px; width: 304px; height: 304px; border-radius: 50%; background: var(--paper); display: flex; align-items: center; justify-content: center; text-align: center; }
  .seal-name { color: var(--honey); font-weight: 700; font-size: 30px; line-height: 1.15; }
  .seal-stem { position: absolute; left: 473px; top: 360px; width: 120px; height: 420px; background: var(--honey); }

  /* label body */
  .body-band { position: absolute; left: 0; top: 775px; width: 1062px; height: 425px; background: var(--honey); }
  .bee-deco { position: absolute; left: 676px; top: 900px; width: 386px; height: 300px; border-radius: 60% 0 0 0; background: linear-gradient(135deg, rgba(217,163,92,0.25), rgba(217,163,92,0.7)); }

  .brand { position: absolute; left: 25px; top: 808px; color: var(--gold); font-weight: 700; font-size: 30px; }
  .contact { position: absolute; left: 25px; top: 854px; color: var(--gold); font-size: 14.5px; line-height: 19px; margin: 0; font-style: normal; }
  .origin { position: absolute; left: 25px; top: 1002px; color: var(--gold); font-size: 14.5px; line-height: 19px; }
  .origin-title { font-family: "Kaushan Script", cursive; font-size: 17px; }
  .origin p { margin: 0; }
  .origin .glass { margin-top: 10px; }
  .best-before { position: absolute; left: 21px; top: 1093px; width: 196px; height: 82px; background: var(--paper); box-sizing: border-box; padding: 4px 6px; font-size: 11.5px; color: var(--ink); font-weight: 700; }

  .variety-line { position: absolute; left: 334px; top: 842px; width: 440px; text-align: center; color: var(--gold); font-weight: 700; font-size: 24px; letter-spacing: 0.5px; }
  .variety { position: absolute; left: 280px; top: 845px; width: 560px; text-align: center; color: var(--paper); font-family: "Caveat Brush", cursive; font-size: 270px; line-height: 1; letter-spacing: 6px; }

  .claim { position: absolute; left: 424px; top: 1088px; width: 190px; text-align: center; color: var(--gold); font-family: "Kaushan Script", cursive; font-size: 19px; line-height: 24px; transform: rotate(-8deg); }
  .weight { position: absolute; left: 612px; top: 1074px; width: 72px; height: 84px; }
</style>
</head>
<body>
<main class="label">
  <div class="seal-ring"></div>
  <div class="seal-stem"></div>
  <div class="seal-face"><span class="seal-name">Imkerei<br>Wiesbrook</span></div>

  <section class="body-band"></section>
  <div class="bee-deco" role="img" aria-label="Große, blasse Biene mit Waben als Dekoration"></div>

  <div class="brand">Wiesbrook</div>
  <address class="contact">
    Lindenkamp 12<br>
    48999 Heidbrook<br>
    01234 567890<br>
    imkerei-wiesbrook.de
  </address>

  <div class="origin">
    <div class="origin-title">Honig aus Deutschland</div>
    <p>Trocken, dunkel und vor<br>Wärme geschützt lagern</p>
    <p class="glass">Mehrwegglas</p>
  </div>

  <div class="best-before">Mindestens haltbar bis:</div>

  <div class="variety-line">HEIDBROOKER LANDHONIG</div>
  <h1 class="variety" style="margin:0;font-weight:400;">Linde</h1>

  <div class="claim">Echter Honig aus<br>dem Münsterland!</div>
  <svg class="weight" viewBox="0 0 72 84" aria-label="500 g">
    <polygon points="36,2 70,21 70,63 36,82 2,63 2,21" fill="#f5c518" transform="rotate(-8 36 42)"/>
    <text x="36" y="50" text-anchor="middle" font-family="Quicksand, sans-serif" font-weight="700" font-size="20" fill="#ffffff" transform="rotate(-8 36 42)">500 g</text>
  </svg>
</main>
</body>
</html>
```